" A Vardim Soluçoes Ambientais é uma empresa que presta serviços de regularizaçao ambiental. Trata-se de uma consultoria ambiental cujo principal serviço é oferecer soluçoes ambientais para atividades produtivas e imóveis urbanos ou rurais. Exemplos: (i) correçao de matrículas e registros em órgao públicos para fazendas produtivas; (ii) correçao de emissoes atmosféricas, ruídos, resíduos, etc, de indústrias; (iii) descontaminaçao do solo ou água subterrânea de um imóvel; (iv) elaboraçao de laudos técnicos sobre passivos ambientais. Observaçao importante: a empresa nao é uma ONG, embora o apelo seja ambiental. "

```html
<!DOCTYPE html>
<html lang="pt-BR">
<head>
<meta charset="utf-8">
<title>Vardim Soluçoes Ambientais — Envelope</title>
<link href="https://fonts.googleapis.com/css2?family=Raleway:wght@400;500&display=swap" rel="stylesheet">
<style>
  :root {
    --canvas-bg: #e9eae8;
    --envelope-green: #2f4d49;
    --envelope-shade: #284441;
    --panel-white: #ffffff;
    --map-grey: #dfe2e2;
    --brand-ink: #2f4d49;
    --tagline-olive: #8a8a6a;
    --contact-grey: #6f7a78;
    --rule-gold: #a39a6e;
    --strip-text: #7f9894;
  }
  * { margin: 0; padding: 0; box-sizing: border-box; }
  html, body {
    width: 1200px;
    height: 1200px;
    overflow: hidden;
    background: var(--canvas-bg);
  }
  .canvas {
    position: relative;
    width: 1200px;
    height: 1200px;
    overflow: hidden;
    font-family: "Raleway", sans-serif;
  }
  .envelope-body {
    position: absolute;
    inset: 0;
  }
  .front-panel {
    position: absolute;
    left: 285px;
    top: 350px;
    width: 630px;
    height: 330px;
    background: var(--panel-white);
    overflow: hidden;
  }
  .map-area {
    position: absolute;
    left: 0;
    top: 0;
    width: 300px;
    height: 100%;
    background: radial-gradient(ellipse 70% 60% at 35% 55%, var(--map-grey) 0%, rgba(223,226,226,0.5) 55%, rgba(255,255,255,0) 100%);
  }
  .brand {
    position: absolute;
    left: 0;
    right: 0;
    top: 118px;
    text-align: center;
  }
  .brand-name {
    font-size: 66px;
    font-weight: 400;
    letter-spacing: 4px;
    color: var(--brand-ink);
    line-height: 1;
  }
  .brand-tagline {
    margin-top: 6px;
    font-size: 13px;
    font-weight: 500;
    letter-spacing: 6px;
    color: var(--tagline-olive);
    text-transform: uppercase;
  }
  .contact-block {
    position: absolute;
    left: 0;
    right: 0;
    top: 258px;
    text-align: center;
    font-size: 10px;
    font-style: normal;
    line-height: 13px;
    color: var(--contact-grey);
  }
  .gold-rule {
    position: absolute;
    left: 285px;
    top: 688px;
    width: 630px;
    height: 9px;
    background: var(--rule-gold);
  }
  .strip-note {
    position: absolute;
    left: 285px;
    top: 712px;
    width: 630px;
    text-align: center;
    font-size: 9px;
    letter-spacing: 1px;
    color: var(--strip-text);
    text-transform: uppercase;
  }
</style>
</head>
<body>
<div class="canvas">
  <svg class="envelope-body" width="1200" height="1200" viewBox="0 0 1200 1200" aria-hidden="true">
    <polygon points="260,330 940,330 940,1010 600,830 260,1010" fill="var(--envelope-green)"/>
    <polygon points="260,330 600,200 940,330" fill="var(--envelope-shade)"/>
  </svg>

  <section class="front-panel">
    <div class="map-area" role="img" aria-label="Faint grey world map showing the Americas"></div>
    <div class="brand">
      <div class="brand-name">VARDIM</div>
      <div class="brand-tagline">Soluções Ambientais</div>
    </div>
    <address class="contact-block">
      contato@vardimambiental.com.br<br>
      +55 11 3456 7890<br>
      rua das acácias 215 · 3º andar · pinheiros · 05422 000 · são paulo sp · brasil<br>
      +55 11 3456 7891
    </address>
  </section>

  <div class="gold-rule"></div>
  <p class="strip-note">regularização ambiental para imóveis e atividades produtivas</p>
</div>
</body>
</html>
```